Veltrano.co - Polar Expeditions Specialists

We need a modern, visually striking business card for Veltrano.co, a company specialized in selling expedition cruises to the most remote regions on Earth, with a focus on the Arctic and Antarctica. The design should instantly communicate that the cardholder is an expert in polar travel. Use clean, premium aesthetics with cool tones like icy blue and white, possibly incorporating polar imagery (ice, glaciers, penguins, etc.)

Attached the logo

Contact Information for Business Card

Feels high-end and trustworthy.. Visually memorable — encourages people to keep it

Colors
0054AA
0677BA
7BADD7
CADEEF
E8F1F8

Requirements
Must have
• ice, glaciers, penguins, montains
Nice to have
• modern, transparente,

```html
<!DOCTYPE html>
<html lang="en">
<head>
<meta charset="utf-8">
<title>Veltrano.co – Business Card</title>
<link href="https://fonts.googleapis.com/css2?family=Montserrat:wght@400;700&family=Poppins:wght@600;700&display=swap" rel="stylesheet">
<style>
  :root {
    --page: #ebecee;
    --card-white: #ffffff;
    --brand-blue: #2c78be;
    --ice-blue: #5b94c9;
    --ice-light: #7badd7;
    --ice-pale: #cadeef;
    --ink: #474a4f;
    --white: #ffffff;
  }
  * { margin: 0; padding: 0; box-sizing: border-box; }
  html, body {
    width: 1192px; height: 1200px; overflow: hidden;
    background: var(--page);
  }
  .canvas { position: relative; width: 1192px; height: 1200px; }

  .card {
    position: absolute; left: 219px; width: 753px; height: 432px;
    border-radius: 48px; overflow: hidden;
    box-shadow: 0 14px 30px rgba(0,0,0,0.12);
  }
  .card--front { top: 145px; background: var(--card-white); }
  .card--back { top: 622px; background: var(--ice-blue); }

  .brand { position: absolute; display: flex; flex-direction: column; }
  .brand__row { display: flex; align-items: center; }
  .brand__dot { border-radius: 50%; flex: none; }
  .brand__name {
    font-family: "Poppins", sans-serif; font-weight: 700; letter-spacing: -0.5px;
    line-height: 1;
  }
  .brand__tagline { font-family: "Poppins", sans-serif; font-weight: 600; }

  .card--front .brand { left: 64px; top: 196px; }
  .card--front .brand__dot { width: 34px; height: 34px; margin-right: 14px; background: var(--brand-blue); }
  .card--front .brand__name { font-size: 37px; color: var(--brand-blue); }
  .card--front .brand__tagline { font-size: 12px; color: var(--brand-blue); margin: 6px 0 0 48px; }

  .divider {
    position: absolute; left: 376px; top: 114px; width: 1.5px; height: 204px;
    background: var(--brand-blue);
  }

  .contact { position: absolute; left: 407px; top: 113px; font-family: "Montserrat", sans-serif; color: var(--ink); }
  .contact__name { font-size: 29px; font-weight: 700; color: var(--brand-blue); letter-spacing: 0.5px; line-height: 1; }
  .contact__title { font-size: 19.5px; line-height: 1.2; margin-top: 2px; }
  .contact__address { font-size: 18px; line-height: 23px; margin-top: 18px; }
  .contact__list { list-style: none; margin-top: 16px; }
  .contact__item { display: flex; align-items: center; font-size: 18.5px; line-height: 29px; }
  .contact__icon { width: 14px; height: 14px; margin-right: 7px; flex: none; }

  .photo-fill {
    position: absolute; inset: 0;
    background: radial-gradient(ellipse 45% 55% at 52% 48%, #88b3da 0%, #6a9fcf 45%, var(--ice-blue) 80%),
                linear-gradient(180deg, #5c95ca 0%, #5b93c8 60%, #5a90c4 100%);
  }

  .card--back .brand { left: 133px; top: 180px; }
  .card--back .brand__dot { width: 70px; height: 70px; margin-right: 20px; background: var(--white); }
  .card--back .brand__name { font-size: 60px; color: var(--white); }
  .card--back .brand__tagline { font-size: 19px; color: var(--white); margin: 10px 0 0 90px; }
</style>
</head>
<body>
<main class="canvas">

  <section class="card card--front" aria-label="Card front">
    <div class="brand">
      <div class="brand__row">
        <span class="brand__dot"></span>
        <span class="brand__name">Veltrano.co</span>
      </div>
      <span class="brand__tagline">Polar Expeditions Specialists</span>
    </div>

    <div class="divider"></div>

    <div class="contact">
      <h1 class="contact__name">MARTIN HOLLOWAY</h1>
      <p class="contact__title">CEO / Founder</p>
      <p class="contact__address">P.O. Box 3129 Harbour Lane<br>Northfjord Region AV 7810</p>
      <ul class="contact__list">
        <li class="contact__item">
          <svg class="contact__icon" viewBox="0 0 16 16" aria-hidden="true"><path fill="#2c78be" d="M1 6c0-2 3-3 7-3s7 1 7 3v1h-3V5.5H4V7H1zM3 8h10l1 6H2zm5 1.5a2 2 0 1 0 0 4 2 2 0 0 0 0-4z"/></svg>
          +43 660 21 48 375
        </li>
        <li class="contact__item">
          <svg class="contact__icon" viewBox="0 0 16 16" aria-hidden="true"><path fill="#2c78be" d="M1 6l7-5 7 5v9H1zm1.5 1.2V13.5L6 10zM8 10.5l-4.8 3.5h9.6zM13.5 7.2L10 10l3.5 3.5z"/></svg>
          martin.holloway@veltrano.co
        </li>
        <li class="contact__item">
          <svg class="contact__icon" viewBox="0 0 16 16" aria-hidden="true"><circle cx="8" cy="8" r="7" fill="#2c78be"/><path fill="#fff" d="M4 4c2 0 3 1 2.5 2.5S4 7 4.5 9 3 10 2.5 8.5 2.5 5 4 4zm6 3c1.5 0 3 1 2.5 3s-2 3-3 2 .5-2-.5-3 0-2 1-2z"/></svg>
          www.veltrano.co
        </li>
      </ul>
    </div>
  </section>

  <section class="card card--back" aria-label="Card back">
    <div class="photo-fill" role="img" aria-label="Photograph of a polar bear walking on snow, tinted icy blue"></div>
    <div class="brand">
      <div class="brand__row">
        <span class="brand__dot"></span>
        <span class="brand__name">Veltrano.co</span>
      </div>
      <span class="brand__tagline">Polar Expeditions Specialists</span>
    </div>
  </section>

</main>
</body>
</html>
```